Quorva - corporate Business Card

We need a good look and innovative business card for a new start up company based in Los Angeles called "Quorva". We are in a payment business, including payment card, app, and ewallet. We are expert in online payment and Card not present (CNP) transaction.
We need an innovative, modern business card.

Our logo font is Aero Matics

Target Market(s)

Startup - Bank - Online Payment - Card Manufacturing

Industry/Entity Type

Startup

Contact Information for Business Card

phone: 555 014 7396 - Address: 4172 Marlowe blvd, Alder City, CA 90299

Requirements
Must have
• Message: innovative, professional, expert, high tech, trust, online payment expert, security
Nice to have
• no comment
Should not have
• no Comment

```html
<!DOCTYPE html>
<html lang="en">
<head>
<meta charset="utf-8">
<title>Quorva – Business Card</title>
<link rel="stylesheet" href="https://fonts.googleapis.com/css2?family=Saira:wght@500;600&family=Nunito+Sans:wght@400;600&display=swap">
<style>
  :root {
    --brand-red: #b71d2d;
    --ink: #2a2a2a;
    --card: #ffffff;
    --backdrop: #e9e6e4;
    --shadow: rgba(0, 0, 0, 0.12);
  }
  * { margin: 0; padding: 0; box-sizing: border-box; }
  html, body {
    width: 1200px;
    height: 900px;
    overflow: hidden;
    background: var(--backdrop);
  }
  .stage { position: relative; width: 1200px; height: 900px; }

  .card {
    position: absolute;
    width: 556px;
    height: 342px;
    background: var(--card);
    border-radius: 18px;
    box-shadow: 0 6px 20px var(--shadow);
  }
  .card--front { left: 238px; top: 62px; }
  .card--back  { left: 459px; top: 518px; }

  .brand-name {
    position: absolute;
    font-family: "Saira", sans-serif;
    font-weight: 600;
    line-height: 1;
    color: var(--brand-red);
    white-space: nowrap;
  }
  .card--front .brand-name {
    left: 50px; top: 150px;
    width: 218px;
    text-align: center;
    font-size: 42px;
  }

  .divider {
    position: absolute;
    left: 277px; top: 93px;
    width: 2px; height: 158px;
    background: var(--brand-red);
    opacity: 0.8;
  }

  .details {
    position: absolute;
    left: 305px; top: 88px;
    font-family: "Nunito Sans", sans-serif;
    color: var(--ink);
  }
  .details__name {
    font-family: "Saira", sans-serif;
    font-weight: 600;
    font-size: 28px;
    line-height: 1;
    color: var(--brand-red);
    white-space: nowrap;
  }
  .details__role { font-size: 16px; margin-top: 3px; }
  .details__contacts { list-style: none; margin-top: 14px; font-size: 15px; line-height: 22px; }
  .details__label { color: var(--brand-red); font-weight: 600; margin-right: 8px; }
  .details__address { margin-top: 15px; font-size: 15px; line-height: 20px; }

  .card--back .brand-name {
    left: 0; top: 136px;
    width: 556px;
    text-align: center;
    font-size: 62px;
    letter-spacing: 1px;
  }
</style>
</head>
<body>
<main class="stage">
  <section class="card card--front" aria-label="Business card front">
    <span class="brand-name">Quorva</span>
    <span class="divider" aria-hidden="true"></span>
    <div class="details">
      <h1 class="details__name">Dana Whitfield</h1>
      <p class="details__role">Director</p>
      <ul class="details__contacts">
        <li><span class="details__label">M:</span>555 014 7396</li>
        <li><span class="details__label">W:</span>www.quorva.com</li>
      </ul>
      <p class="details__address">4172 Marlowe blvd,<br>Alder City, CA 90299</p>
    </div>
  </section>

  <section class="card card--back" aria-label="Business card back">
    <span class="brand-name">Quorva</span>
  </section>
</main>
</body>
</html>
```